Kestrelford Therapy and Consulting

Build & publish a WordPress website that advertises and markets my private practice - which is delivering, and consulting in, psychological therapies. I also need to be able to edit content (eg text and images) on the end product thereafter. It should have a call to action on the homepage, links to:
• About me
• For referrers (with link to service fees)
• Contact details – phone#, email address, location, operating hours, and service fees
• Other resources

Target Market(s)

People struggling with mental health, relationships, and/or psychological disorders

Industry/Entity Type

Mental health

Coding

Coded - Design and coding required

Number of Pages Required

4 page

Requirements
Must have
• WordPress
Nice to have
• Please make my logo standout on the home page
Should not have
• No testimonials - they're forbidden for psychologists in Australia

```html
<!DOCTYPE html>
<html lang="en">
<head>
<meta charset="utf-8">
<title>Kestrelford Therapy and Consulting</title>
<link rel="stylesheet" href="https://fonts.googleapis.com/css2?family=Lora:wght@400;500&family=Mulish:wght@400;600;700&display=swap">
<style>
:root{
  --light:#eef6fc;
  --cyan:#3ec8dc;
  --purple:#c172d4;
  --purple-dark:#a96bc4;
  --blue:#6b8ed6;
  --ink:#222;
  --text:#555;
  --white:#fff;
  --serif:'Lora',Georgia,serif;
  --sans:'Mulish',Arial,sans-serif;
}
*{box-sizing:border-box;margin:0;padding:0}
html,body{width:1200px;height:5357px;overflow:hidden}
body{font-family:var(--sans);color:var(--text);background:var(--white);position:relative}
section,header,footer{position:absolute;left:0;width:1200px}
.abs{position:absolute}
.heading{font-family:var(--serif);font-weight:400;color:var(--ink)}
.rule{position:absolute;height:4px;width:48px;background:var(--ink)}
.brand{display:flex;align-items:center;gap:12px;font-family:var(--serif);font-size:19px;color:#666}
.brand-dot{width:30px;height:30px;border-radius:50%;background:var(--cyan)}

/* hero */
.hero{top:0;height:676px;background:var(--light)}
.hero-photo{left:516px;top:0;width:551px;height:676px;background:linear-gradient(160deg,#3f5a34,#6b7a5c 45%,#3c5b87)}
.main-nav{left:516px;top:0;display:flex;font-family:var(--serif);font-size:17px}
.main-nav a{color:var(--white);text-decoration:none;height:66px;line-height:66px;padding:0 34px}
.main-nav a.current{background:var(--cyan)}
.hero-name{left:130px;top:122px;font-size:42px}
.hero-role{left:132px;top:186px;font-size:14px;font-weight:600;color:var(--ink)}
.hero-intro{left:132px;top:230px;width:334px;font-size:13px;line-height:21px;text-align:justify}
.hero-qual-label{left:132px;top:430px;font-size:13px;color:var(--ink)}
.hero-qual{left:132px;top:460px;font-family:var(--serif);font-size:16px;color:var(--ink)}
.hero-email{left:135px;top:516px;width:256px;height:46px;border:2px solid #444;display:flex;align-items:center;gap:12px;padding-left:14px;font-size:16px;color:var(--ink)}
.info-card{top:607px;height:107px;color:var(--white);padding:22px 24px}
.info-card h3{font-family:var(--serif);font-weight:500;font-size:15px;text-transform:uppercase;margin-bottom:6px}
.info-card p{font-size:12px;line-height:19px;opacity:.9}
.card-location{left:135px;width:320px;background:var(--cyan)}
.card-phone{left:478px;width:256px;background:var(--purple);display:flex;align-items:center;gap:14px}
.card-phone strong{font-size:24px;letter-spacing:.5px}
.card-hours{left:763px;width:289px;background:var(--blue)}

/* services */
.services{top:676px;height:549px;text-align:center}
.services .heading{position:absolute;top:98px;width:100%;font-size:34px}
.services-intro{position:absolute;top:162px;left:300px;width:600px;font-size:16px;line-height:27px}
.services .rule{top:250px;left:576px}
.service-list{position:absolute;top:316px;left:110px;display:flex}
.service{height:160px;padding:30px 18px 0;border-right:2px solid #9fd8e3;font-family:var(--serif);font-size:15px;color:var(--ink)}
.service:last-child{border-right:0}
.service-icon{width:54px;height:54px;margin:0 auto 24px;border-radius:50%;background:linear-gradient(135deg,var(--purple),var(--cyan))}

/* interests */
.interests{top:1225px;height:830px;background:linear-gradient(100deg,#4e4a49,#6d615c 40%,#3b3735)}
.interests .heading{position:absolute;top:52px;width:100%;text-align:center;color:var(--white);font-size:34px}
.interests .rule{top:134px;left:576px;background:var(--white)}
.interest-grid{position:absolute;top:189px;left:166px;display:grid;grid-template-columns:425px 425px;column-gap:23px;row-gap:17px}
.interest{height:58px;background:#f3f3f3;display:flex;align-items:center;gap:22px;padding-left:22px;font-family:var(--serif);font-size:16px;color:var(--ink)}
.interest-icon{width:32px;height:32px;border-radius:50%;background:linear-gradient(135deg,var(--purple),var(--cyan))}

/* modalities */
.modalities{top:2055px;height:653px}
.mod-circle{width:137px;text-align:center;font-size:13px;color:var(--ink)}
.mod-circle span{display:block;width:137px;height:137px;border-radius:50%;margin-bottom:8px}
.modalities .heading{position:absolute;left:666px;top:70px;font-size:36px}
.modalities .rule{left:666px;top:144px}
.mod-text{left:666px;width:390px;font-size:15px;line-height:27px;text-align:justify}

/* associations */
.associations{top:2708px;height:166px;background:var(--blue);color:var(--white)}
.associations h2{position:absolute;left:133px;top:36px;font-family:var(--serif);font-weight:400;font-size:34px;line-height:44px}
.assoc{top:40px;height:98px;border-left:2px solid rgba(255,255,255,.6);padding-left:40px;font-size:16px;line-height:25px;display:flex;align-items:center}

/* quality & background */
.quality{top:2874px;height:974px;background:var(--light)}
.quality .heading{font-size:36px}
.quality-text{font-size:14px;line-height:26px;text-align:justify}
.photo{border-radius:0}

/* fees */
.fees{top:3848px;height:453px}
.fees .heading{position:absolute;top:58px;width:100%;text-align:center;font-size:34px}
.fees .rule{top:124px;left:576px}
.fee{top:166px;width:293px;height:219px;background:var(--blue);color:var(--white);font-family:var(--serif);font-size:18px;line-height:29px;text-align:center;display:flex;align-items:center;justify-content:center;padding:0 46px}

/* payment band */
.band{top:4301px;height:321px}
.band-half{top:0;height:321px;color:var(--white)}
.band-left{left:0;width:589px;background:var(--purple)}
.band-right{left:589px;width:611px;background:var(--purple-dark)}
.band-icon{position:absolute;top:128px;width:100px;height:100px;border-radius:50%;background:var(--white);display:flex;align-items:center;justify-content:center}
.band-half h3{position:absolute;font-family:var(--serif);font-weight:400;font-size:32px;line-height:36px}
.band-half p{position:absolute;font-size:14px;line-height:21px;opacity:.92}

/* referrers */
.referrers{top:4622px;height:532px}
.referrers .heading{position:absolute;left:131px;top:60px;font-size:36px}
.referrers .rule{left:131px;top:122px}
.ref-text{position:absolute;left:131px;top:160px;width:385px;font-size:15px;line-height:25px;text-align:justify}
.btn{position:absolute;left:131px;top:416px;width:120px;height:42px;background:var(--purple);color:var(--white);font-family:var(--serif);font-size:15px;display:flex;align-items:center;justify-content:center;text-decoration:none}
.ref-photo{left:589px;top:0;width:611px;height:532px;background:linear-gradient(150deg,#d9d4cc,#b9c3cf 50%,#8aa2c0)}

/* footer */
.site-footer{top:5154px;height:203px;background:var(--light)}
.site-footer .brand{position:absolute;left:131px;top:52px}
.foot-nav{position:absolute;left:592px;top:58px;display:flex;gap:58px;font-family:var(--serif);font-size:16px}
.foot-nav a{color:var(--ink);text-decoration:none}
.foot-line{position:absolute;left:131px;top:119px;width:939px;height:1px;background:#9fd8e3}
.copyright{position:absolute;top:152px;width:100%;text-align:center;font-size:12px;color:var(--ink)}
</style>
</head>
<body>

<header class="hero">
  <div class="abs brand" style="left:130px;top:30px"><span class="brand-dot"></span>Kestrelford Therapy and Consulting</div>
  <div class="abs hero-photo" role="img" aria-label="Portrait photograph of the psychologist outdoors"></div>
  <nav class="abs main-nav">
    <a class="current" href="#">Home</a><a href="#">About Me</a><a href="#">Services</a><a href="#">Contact Me</a>
  </nav>
  <h1 class="abs heading hero-name">Mr Daniel Ashworth</h1>
  <p class="abs hero-role">Clinical Psychologist, Clinical Supervisor</p>
  <p class="abs hero-intro">I'm a clinical psychologist, psychotherapist, EMDR Consultant, and Resource Therapy Practitioner and Trainer. My main interest in therapy is helping people overcome the inner obstacles that cause them emotional pain and suffering, and that maintain behavioural patterns that are damaging or self-defeating. I also like to train, coach and mentor other therapists in effective therapies.</p>
  <p class="abs hero-qual-label">QUALIFICATIONS</p>
  <p class="abs hero-qual">BAppSc(Hons), MPsych(Clin)</p>
  <div class="abs hero-email">
    <svg width="20" height="14" viewBox="0 0 20 14" fill="none" stroke="#333" stroke-width="1.5"><rect x="1" y="1" width="18" height="12"/><path d="M1 1l9 7 9-7"/></svg>
    info@kestrelford.com
  </div>
  <div class="abs info-card card-location">
    <h3>Practice Locations</h3>
    <p>Suite 4, Harbour House,<br>18 Wren Street, Kestrelford, TAS 7000</p>
  </div>
  <div class="abs info-card card-phone">
    <svg width="36" height="36" viewBox="0 0 24 24" fill="none" stroke="#fff" stroke-width="1.4"><path d="M5 3h4l2 5-2.5 1.5a11 11 0 0 0 6 6L16 13l5 2v4a2 2 0 0 1-2 2A17 17 0 0 1 3 5a2 2 0 0 1 2-2z"/></svg>
    <div><h3 style="margin-bottom:2px">Phone</h3><strong>0412 555 218</strong></div>
  </div>
  <div class="abs info-card card-hours">
    <h3>Appointments</h3>
    <p>Currently I am available between<br>9am to 5pm on Wednesdays only.</p>
  </div>
</header>

<section class="services">
  <h2 class="heading">Services</h2>
  <p class="services-intro">I provide trauma-focused psychotherapy to clients and consult with other mental health clinicians on their practice of psychotherapy.</p>
  <div class="rule"></div>
  <div class="service-list">
    <div class="service" style="width:158px"><div class="service-icon" role="img" aria-label="Psychotherapy icon"></div>Psychotherapy</div>
    <div class="service" style="width:140px"><div class="service-icon" role="img" aria-label="Assessment icon"></div>Assessment</div>
    <div class="service" style="width:215px"><div class="service-icon" role="img" aria-label="Professional training icon"></div>Professional Training</div>
    <div class="service" style="width:215px"><div class="service-icon" role="img" aria-label="Clinical supervision icon"></div>Clinical Supervision</div>
    <div class="service" style="width:260px"><div class="service-icon" role="img" aria-label="Online video consultations icon"></div>Online Video Consultations</div>
  </div>
</section>

<section class="interests" role="img" aria-label="Background photograph of a counselling conversation">
  <h2 class="heading">Areas Of Special Interest</h2>
  <div class="rule"></div>
  <div class="interest-grid">
    <div class="interest"><span class="interest-icon"></span>Addiction</div>
    <div class="interest"><span class="interest-icon"></span>Dual diagnosis</div>
    <div class="interest"><span class="interest-icon"></span>Anger Related Issues</div>
    <div class="interest"><span class="interest-icon"></span>Existential Issues</div>
    <div class="interest"><span class="interest-icon"></span>Anxiety / Panic Attacks</div>
    <div class="interest"><span class="interest-icon"></span>Grief / Bereavement</div>
    <div class="interest"><span class="interest-icon"></span>Assertiveness</div>
    <div class="interest"><span class="interest-icon"></span>Personality Disorders</div>
    <div class="interest"><span class="interest-icon"></span>Borderline Personality</div>
    <div class="interest"><span class="interest-icon"></span>Phobias</div>
    <div class="interest"><span class="interest-icon"></span>Depression</div>
    <div class="interest"><span class="interest-icon"></span>PTSD</div>
    <div class="interest"><span class="interest-icon"></span>Dissociative Disorders</div>
    <div class="interest"><span class="interest-icon"></span>Relationship Issues</div>
    <div class="interest"><span class="interest-icon"></span>Trauma Recovery</div>
    <div class="interest"><span class="interest-icon"></span>Self Development</div>
  </div>
</section>

<section class="modalities">
  <div class="abs mod-circle" style="left:131px;top:62px"><span role="img" aria-label="EMDR session photograph" style="background:linear-gradient(135deg,#d8d2cb,#8c7b6e)"></span>EMDR</div>
  <div class="abs mod-circle" style="left:287px;top:62px"><span role="img" aria-label="Existential therapy photograph" style="background:radial-gradient(circle,#c07a3a,#3a2418)"></span>Existential</div>
  <div class="abs mod-circle" style="left:449px;top:62px"><span role="img" aria-label="Integrative therapy photograph" style="background:linear-gradient(135deg,#e2e0dc,#9aa0a8)"></span>Integrative</div>
  <div class="abs mod-circle" style="left:131px;top:248px"><span role="img" aria-label="Mindfulness photograph" style="background:linear-gradient(135deg,#e7d6b4,#b59670)"></span>Mindfulness</div>
  <div class="abs mod-circle" style="left:287px;top:248px"><span role="img" aria-label="Person centred therapy photograph" style="background:linear-gradient(180deg,#d8c0a8,#6f5d52)"></span>Person Centred</div>
  <div class="abs mod-circle" style="left:449px;top:248px"><span role="img" aria-label="Psychodynamic therapy photograph" style="background:linear-gradient(135deg,#c9c6c2,#5d6470)"></span>Psychodynamic</div>
  <div class="abs mod-circle" style="left:208px;top:431px"><span role="img" aria-label="Schema therapy photograph" style="background:radial-gradient(circle,#8fb3ad,#2d4b4a)"></span>Schema Therapy</div>
  <div class="abs mod-circle" style="left:359px;top:431px"><span role="img" aria-label="CBT photograph" style="background:linear-gradient(135deg,#6a5f58,#1e1a18)"></span>CBT</div>
  <h2 class="heading">Modalities / Approach</h2>
  <div class="rule"></div>
  <p class="abs mod-text" style="top:186px">I believe that using Eye Movement Desensitizing and Reprocessing (EMDR) therapy and Resource Therapy (RT) together addresses almost all mental illness that doesn't involve an organic component.</p>
  <p class="abs mod-text" style="top:363px">EMDR principally addresses disturbing memories from the past that negatively impact a person in the present. RT addresses resource states (also known as states of mind, parts, ego states, and schema modes) that are putting a person 'out of balance', i.e. they are yielding unwanted emotions or unwanted behaviours that are impairing a person's ability to function.</p>
</section>

<section class="associations">
  <h2>Professional<br>Associations</h2>
  <div class="abs assoc" style="left:383px;width:195px">National<br>Psychology<br>Guild</div>
  <div class="abs assoc" style="left:576px;width:275px">EMDR Practitioners<br>Network (Accredited<br>Practitioner &amp; Consultant)</div>
  <div class="abs assoc" style="left:853px;width:250px;line-height:24px">Parts Therapy<br>Collective (Clinical<br>Resource Therapist<br>&amp; Trainer</div>
</section>

<section class="quality">
  <h2 class="abs heading" style="left:133px;top:70px">Quality Provision</h2>
  <div class="rule" style="left:133px;top:138px;width:118px"></div>
  <p class="abs quality-text" style="left:133px;top:180px;width:390px">I generally start sessions checking with how clients are feeling and coping between sessions, ascertaining whether or not the client believes we are "on track" according to what was agreed in the treatment plan we co-created. I endeavour to maximise the benefit we can obtain from the number of sessions available to us.</p>
  <div class="abs photo" style="left:599px;top:59px;width:470px;height:353px;background:linear-gradient(135deg,#c9d4d8,#8a9ea6 55%,#7a3a4d)" role="img" aria-label="Photograph of a client in a counselling session"></div>

  <div class="abs photo" style="left:133px;top:475px;width:470px;height:426px;background:linear-gradient(160deg,#3f5a34,#6b7a5c 45%,#3c5b87)" role="img" aria-label="Portrait photograph of the psychologist"></div>
  <h2 class="abs heading" style="left:666px;top:475px">Background</h2>
  <div class="rule" style="left:666px;top:540px;width:118px"></div>
  <p class="abs quality-text" style="left:666px;top:570px;width:408px;font-size:14px;line-height:25.6px">When I first started to practice, I felt ill-prepared for the vast range of maladies of the human condition, especially as I was immersed in a setting that had so many suffering from the impact of trauma in childhood. Thus, I embarked on decade long learning plan that got me where I am now –equipped with the therapies my practice-based evidence tells me I need, and that satisfies the need for evidence-based practice. I am now substantially trained in EMDR and Resource Therapies, such that I can effectively treat adult survivors of childhood trauma, and supervise or coach others in trauma focused therapies that are effective alone, or in combination.</p>
</section>

<section class="fees">
  <h2 class="heading">Fees</h2>
  <div class="rule"></div>
  <div class="abs fee" style="left:131px">My standard fee for a 50 to 60 minute psychological therapy session is $220.</div>
  <div class="abs fee" style="left:447px">For those who are on low or no income my concession fee is $180.</div>
  <div class="abs fee" style="left:774px">Medicare currently rebates 137.05 for a 50+ minute psychological therapy session if a MHCP is in place.</div>
</section>

<section class="band">
  <div class="abs band-half band-left">
    <div class="band-icon" style="left:131px">
      <svg width="50" height="40" viewBox="0 0 50 40" fill="none" stroke="#c172d4" stroke-width="3"><rect x="2" y="4" width="40" height="28" rx="3"/><path d="M2 13h40"/><circle cx="40" cy="30" r="8" fill="#fff"/><path d="M36 30l3 3 5-6"/></svg>
    </div>
    <h3 style="left:272px;top:70px">Payment Options</h3>
    <p style="left:274px;top:118px;width:270px">I currently accept EFT transfers only. I can process Medicare webclaims online on behalf of clients where they are registered with Medicare, i.e. Medicare already have their bank account details on file to be able to deposit the rebate into.</p>
  </div>
  <div class="abs band-half band-right">
    <div class="band-icon" style="left:56px;top:113px">
      <svg width="44" height="50" viewBox="0 0 44 50" fill="none" stroke="#a96bc4" stroke-width="3"><path d="M22 47s-16-16-16-27a16 16 0 0 1 32 0c0 11-16 27-16 27z"/><path d="M17 27V12h7a4.5 4.5 0 0 1 0 9h-7"/></svg>
    </div>
    <h3 style="left:210px;top:66px">Transport And<br>Parking</h3>
    <p style="left:210px;top:150px;width:240px">There is limited paid parking in Wren Street and surrounds but, being adjacent to the GPO, Harbour House is very close to public transport.</p>
  </div>
</section>

<section class="referrers">
  <h2 class="heading">For Referrers</h2>
  <div class="rule"></div>
  <p class="ref-text">Lorem ipsum dolor sit amet, consectetur adipiscing elit, sed do eiusmod tempor incididunt ut labore et dolore magna aliqua. Ut enim ad minim veniam, quis nostrud exercitation ullamco laboris nisi ut aliquip ex ea commodo consequat. Duis aute irure dolor in reprehenderit in voluptate velit esse cillum dolore eu fugiat nulla pariatur. Excepteur sint occaecat cupidatat non proident, sunt in culpa qui officia deserunt mollit anim id .</p>
  <a class="btn" href="#">Read More</a>
  <div class="abs ref-photo" role="img" aria-label="Photograph of a therapist taking notes with a client"></div>
</section>

<footer class="site-footer">
  <div class="brand"><span class="brand-dot"></span>Kestrelford Therapy and Consulting</div>
  <nav class="foot-nav"><a href="#">Home</a><a href="#">About Me</a><a href="#">Services</a><a href="#">Contact Me</a></nav>
  <div class="foot-line"></div>
  <p class="copyright">Copyright © 2024 All Rights Reserved</p>
</footer>

</body>
</html>
```